Wordpress Design Project

We need a wordpress design for a new creative innovation company based in Melbourne called BrightForge.
We develop innovative growth and communication strategies for our clients who are generally medium sized businesses wanting to find new ways to grow their businesses.
Our Services include:
Business Strategy
Communications and Strategic Planning
Creative Consultancy
Professional Development
Change Management
Project Management
We would like our wordpress design to be simple and professional yet give a feeling of innovation, kind of like old meeting new.
We are leaning towards the predominant background colour being white, but open to suggestions.
Attached are logo files.
If you require any further information please contact us via the Mosaic Bazaar site.
Communication

```html
<!DOCTYPE html>
<html lang="en">
<head>
<meta charset="utf-8">
<title>BrightForge — Innovative Professional Development</title>
<link href="https://fonts.googleapis.com/css2?family=Noto+Sans:wght@400;700&family=Source+Sans+3:ital,wght@0,400;0,600;0,700;1,400&display=swap" rel="stylesheet">
<style>
:root{
  --green:#7fba2a;
  --green-dark:#6aa31c;
  --green-light:#8cc63f;
  --ink:#3a3d42;
  --text:#555a60;
  --muted:#7a7f85;
  --rule:#e2e2e2;
  --frame:#e9e9ea;
  --bar:#4a4f57;
  --white:#ffffff;
}
*{margin:0;padding:0;box-sizing:border-box}
html,body{width:1057px;height:1200px;overflow:hidden;background:var(--white)}
body{position:relative;font-family:"Source Sans 3",sans-serif;color:var(--text);font-size:12px}
.top-bar{position:absolute;left:0;top:0;width:1057px;height:5px;background:var(--bar)}
.brand{position:absolute;left:49px;top:38px;font-family:"Noto Sans",sans-serif;font-size:39px;letter-spacing:-1.5px;color:var(--green);font-weight:400}
.main-nav{position:absolute;top:54px;left:0;width:1057px;height:38px;font-family:"Noto Sans",sans-serif;font-size:14px;color:var(--ink)}
.main-nav a{position:absolute;top:12px;color:inherit;text-decoration:none}
.main-nav .sep{position:absolute;top:14px;width:1px;height:16px;background:#bbb}
.main-nav .active{top:0;height:38px;padding:12px 18px 0;background:var(--green);color:var(--white)}
.dropdown{position:absolute;left:643px;top:92px;width:249px;height:147px;background:var(--green-light);z-index:5;padding-top:6px}
.dropdown li{list-style:none;height:26.5px;line-height:26.5px;padding-left:20px;font-size:11px;font-family:"Noto Sans",sans-serif;color:#3c5a12;border-bottom:1px solid rgba(255,255,255,.3)}
.dropdown li:last-child{border-bottom:0}
.hero{position:absolute;left:47px;top:120px;width:961px;height:394px;border:4px solid var(--frame);overflow:hidden}
.hero-visual{position:absolute;left:346px;top:0;width:611px;height:386px;background:linear-gradient(90deg,#fff 0%,#e9e9ea 30%,#c9c6cc 60%,#6d6570 100%)}
.hero h1{position:absolute;left:49px;top:62px;font-family:"Noto Sans",sans-serif;font-weight:400;font-size:41px;color:var(--green);letter-spacing:.5px}
.hero h2{position:absolute;left:48px;top:113px;font-family:"Noto Sans",sans-serif;font-weight:400;font-size:24px;color:var(--ink)}
.hero p{position:absolute;left:49px;top:148px;width:330px;font-size:12px;line-height:19px;color:#444}
.btn-quote{position:absolute;left:51px;top:229px;width:135px;height:40px;background:var(--green);color:var(--white);font-family:"Noto Sans",sans-serif;font-size:18px;line-height:40px;text-align:center;box-shadow:0 6px 6px -4px rgba(0,0,0,.2)}
h3{font-family:"Noto Sans",sans-serif;font-weight:400;font-size:17px;color:var(--ink);line-height:21px}
.block{position:absolute;line-height:19px}
.welcome{left:52px;top:542px;width:450px}
.welcome .lead{width:425px;color:var(--green-dark);font-weight:700;margin:8px 0 10px;line-height:19px}
.welcome p+p{margin-top:6px}
.v-rule{position:absolute;width:1px;background:var(--rule)}
.h-rule{position:absolute;left:47px;width:961px;height:1px;background:var(--rule)}
.feature{top:542px;width:210px}
.feature p{width:206px}
.feature .thumb{width:204px;height:91px;margin:9px 0 10px}
.learn{display:block;margin-top:9px;color:var(--green);font-weight:600;font-size:12.5px}
.col{top:849px;width:225px}
.col h3{margin-bottom:10px}
.col .intro{color:#333;margin-bottom:6px}
.services li{list-style:none;font-size:11.5px;color:#444;font-weight:600;padding-left:14px;position:relative;margin-bottom:4.5px}
.services li::before{content:"";position:absolute;left:2px;top:6px;border-left:5px solid var(--green);border-top:4px solid transparent;border-bottom:4px solid transparent}
.post{color:var(--ink);font-weight:600;font-size:12.5px;margin-bottom:18px}
.post small{display:block;font-size:11px;font-weight:400;color:var(--muted);margin-top:3px}
.post small b{color:#555}
.quote{font-style:italic;color:var(--muted);margin-bottom:6px}
.author{font-weight:600;color:#555;font-size:11.5px;margin-bottom:20px}
.footer-rule{position:absolute;left:47px;top:1127px;width:961px;height:4px;background:var(--bar)}
.copyright{position:absolute;left:47px;top:1149px;font-size:11px;color:#444}
.social{position:absolute;left:926px;top:1145px}
</style>
</head>
<body>
<div class="top-bar"></div>
<div class="brand">BrightForge</div>

<nav class="main-nav">
  <a style="left:500px">Home</a><span class="sep" style="left:555px"></span>
  <a style="left:572px">About us</a>
  <a class="active" style="left:643px">Services</a>
  <a style="left:749px">Testimonials</a><span class="sep" style="left:845px"></span>
  <a style="left:863px">Blog</a><span class="sep" style="left:909px"></span>
  <a style="left:926px">Contact</a>
</nav>
<ul class="dropdown">
  <li>Business Strategy</li>
  <li>Communications and Strategic Planning</li>
  <li>Creative Consultancy</li>
  <li>Professional Development</li>
  <li>Change Management</li>
</ul>

<section class="hero">
  <div class="hero-visual" role="img" aria-label="Smiling businesswoman in a grey suit beside a rising bar chart with an orange arrow"></div>
  <h1>INNOVATIVE</h1>
  <h2>PROFESSIONAL DEVELOPMENT</h2>
  <p>Phasellus felis dolor, scelerisque a, tempus eget, lobortis id, libero. Donec scelerisque leo ac risus. Praesent sit amet est. In dictum, dolor eu dictum porttitor, enim felis viverra mi, eget luctus massa purus quis odio.</p>
  <div class="btn-quote">Get a Quote</div>
</section>

<div class="block welcome">
  <h3>Welcome to BrightForge Mainpage</h3>
  <p class="lead">Lorem ipsum dolor sit amet, consectetuer adipiscing elit. Nam cursus.<br>Morbi ut mi. Nullam enim leo, egestas id</p>
  <p>Etiam eu urna. Sed porta. Suspendisse quam leo, molestie sed, luctus quis, feugiat in, pede. Fusce tellus. Sed metus augue, convallis et, vehicula ut, pulvinar eu, ante. Integer orci tellus, tristique vitae, consequat nec, porta vel, lectus. Nulla sit amet diam.</p>
  <p>Nunc tempus felis vitae urna. Vivamus porttitor, neque at volutpat rutrum, purus nisi eleifend libero, a tempus libero lectus feugiat felis. Morbi diam mauris, viverra in, gravida eu, mattis in, ante. Morbi eget arcu. Morbi porta, libero id ullamcorper nonummy, nibh ligula pulvinar metus, eget consectetuer augue nisi quis lacus. Ut ac mi quis lacus mollis aliquam. Curabitur iaculis tempus eros.</p>
</div>
<div class="v-rule" style="left:527px;top:544px;height:277px"></div>

<div class="block feature" style="left:550px">
  <h3 style="padding-left:2px">Creative Consulting<br>and Management</h3>
  <div class="thumb" role="img" aria-label="Light bulb glowing on a grassy field under a bright sky" style="background:linear-gradient(180deg,#cfe3ee 0%,#5b8fb5 45%,#86a85a 80%,#4d6b2c 100%)"></div>
  <p>Curabitur tristique mi condimentum<br>orci. Phasellus pellentesque aliquam enim. Proin dui lectus, cursus eu, mattis laoreet, viverra sit amet, quam.</p>
  <span class="learn">LEARN MORE</span>
</div>
<div class="block feature" style="left:794px">
  <h3>Communications and<br>Strategic Planning</h3>
  <div class="thumb" role="img" aria-label="Business team gathered around a glass board discussing a plan" style="background:linear-gradient(90deg,#dfe4ea 0%,#c8ccd2 50%,#b59a88 100%)"></div>
  <p>Curabitur tristique mi condimentum<br>orci. Phasellus pellentesque aliquam enim. Proin dui lectus, cursus eu, mattis laoreet, viverra sit amet, quam.</p>
  <span class="learn">LEARN MORE</span>
</div>

<div class="h-rule" style="top:821px"></div>
<div class="v-rule" style="left:279px;top:821px;height:272px"></div>
<div class="v-rule" style="left:527px;top:821px;height:272px"></div>
<div class="v-rule" style="left:772px;top:821px;height:272px"></div>

<div class="block col" style="left:50px">
  <h3>How We Work</h3>
  <p class="intro">Phasellus felis dolor, scelerisque a, tempus eget, lobortis id, libero.</p>
  <p>Donec scelerisque leo ac risus. Praesent sit amet est. In dictum, dolor eu dictum porttitor, enim felis viverra mi, eget luctus massa purus quis odio. Etiam nulla massa, pharetra facilisis, volutpat in, imperdiet sit amet, sem. Aliquam nec erat at purus cursus interdum. Vestibulum ligula augue, bibendum accumsan.</p>
</div>
<div class="block col" style="left:301px">
  <h3>Our Services</h3>
  <p class="intro" style="margin-bottom:10px">Donec scelerisque leo ac risus. Praesent sit amet est. In dictum, dolor eu dictum porttitor, enim felis viverra mi.</p>
  <ul class="services">
    <li>Business Strategy</li>
    <li>Communications and Strategic Planning</li>
    <li>Creative Consultancy</li>
    <li>Professional Development</li>
    <li>Change Management</li>
    <li>Project Management</li>
  </ul>
</div>
<div class="block col" style="left:546px;width:210px">
  <h3>Recent Blog Post</h3>
  <p class="post">Praesent metus ipsum, pulvinar pulvinar, porta id, fringilla at, est.<small><b>read</b> more</small></p>
  <p class="post">Maecenas aliquet velit vel turpis. Mauris neque metus, malesuada nec<small><b>read</b> more</small></p>
  <p class="post">Proin nulla arcu, nonummy luctus, dictum eget, fermentum et.<small><b>read</b> more</small></p>
</div>
<div class="block col" style="left:793px;width:210px">
  <h3>Testimonials</h3>
  <p class="quote">Maecenas aliquet velit vel turpis. Mauris neque metus, malesuada nec, ultricies sit amet, porttitor mattis, enim. In massa libero, interdum nec</p>
  <p class="author">By Author Name</p>
  <p class="quote">Maecenas aliquet velit vel turpis. Mauris neque metus, malesuada nec, ultricies sit amet, porttitor mattis, enim. In massa libero, interdum nec</p>
  <p class="author">By Author Name</p>
</div>

<div class="footer-rule"></div>
<p class="copyright">© 2012 Company Name.&nbsp; All right reserved.&nbsp; Term of Use</p>
<svg class="social" width="80" height="24" viewBox="0 0 80 24" aria-label="Social links">
  <circle cx="10" cy="12" r="10" fill="#3f444b"/>
  <circle cx="38" cy="12" r="10" fill="#3f444b"/>
  <circle cx="66" cy="12" r="10" fill="#3f444b"/>
</svg>
</body>
</html>
```